Boutique Real Estate Brokerage Tessly Realty Website Design

Winning designer work on migrate as well through nest ferry.
We need a new website as an informational hub to aid our print and digital strategy as well as showing that we are located in Brooklyn and Florida. I have a boutique real estate brokerage and advisory firm specializing in residential leasing, multifamily sales and 1031 Exchange appropriation. This won't be a portal to search properties, it will be a place for information. I'd like space for an ebook to be downloaded and information on my probate sales and multifamily leasing marketing campaigns. I included my logo and will leave it up to the designer to come up with colors to match it. I have also attached verbiage for each page. The final design should have a modern high end look that reflects gentrifying Brooklyn as well as beautiful Florida.
Thank you!
Target Market(s)
Owners of income producing real estate and develop-able land in Brooklyn, NY and Florida.
Industry/Entity Type
Real Estate
Coding
Coded - Design and coding required
Number of Pages Required
5+ page
Colors
Designer to choose colors to be used in the design.
Requirements
Must have
- A modern elegant look
Nice to have
- pictures of brooklyn and florida
Should not have
- real estate search pages

```html
<!DOCTYPE html>
<html lang="en">
<head>
<meta charset="utf-8">
<title>Tessly Realty</title>
<link href="https://fonts.googleapis.com/css2?family=Audiowide&family=Raleway:wght@400;500;600;700&display=swap" rel="stylesheet">
<style>
:root{
  --black:#0b0b0b;
  --charcoal:#262626;
  --dark:#1d1d1d;
  --white:#ffffff;
  --ink:#2a2a2a;
  --muted:#555555;
  --line:#d8d8d8;
  --light:#c9c9c9;
}
*{margin:0;padding:0;box-sizing:border-box}
html,body{width:1200px;height:4009px;overflow:hidden}
body{font-family:"Raleway",sans-serif;color:var(--ink);background:var(--white);position:relative}
.abs{position:absolute}
.display{font-family:"Audiowide",sans-serif;text-transform:uppercase}

/* header */
.site-header{left:0;top:0;width:1200px;height:107px;background:var(--black)}
.brand{left:90px;top:28px;display:flex;align-items:center;gap:14px;color:var(--white);font-weight:600;font-size:19px;letter-spacing:3px}
.brand-mark{width:48px;height:48px;border-radius:50%;background:#8a8a8a}
.main-nav{left:544px;top:0;height:107px;display:flex;align-items:center;gap:44px;color:var(--white);font-size:17px}
.main-nav .caret{width:0;height:0;border-left:6px solid transparent;border-right:6px solid transparent;border-top:7px solid var(--white);margin-left:-10px}

.top-bar{left:0;top:107px;width:1200px;height:48px;background:var(--white);font-size:15px;color:var(--ink)}
.top-bar .contact{left:90px;top:13px;display:flex;gap:40px}
.top-bar .contact span{display:flex;align-items:center;gap:8px}
.top-bar .account{right:90px;top:13px;display:flex;gap:36px}

/* hero */
.hero{left:0;top:155px;width:1200px;height:631px;background:linear-gradient(100deg,#3c2a22 0%,#7a4a38 35%,#8d5b45 55%,#3f3a2c 80%,#26231c 100%)}
.hero-title{left:0;top:178px;width:1200px;text-align:center;color:var(--white);font-size:34px;line-height:46px;letter-spacing:1px}
.play{left:562px;top:302px;width:74px;height:74px}
.dots{left:542px;top:551px;display:flex;gap:14px}
.dots i{width:14px;height:14px;border:2px solid var(--white);display:block}
.dots i.on{background:var(--white)}

/* intro band */
.intro{left:0;top:786px;width:1200px;height:269px;background:var(--charcoal);color:var(--white)}
.intro h2{left:90px;top:96px;font-weight:500;font-size:27px}
.intro p{left:90px;top:136px;font-size:17px;color:#d6d6d6}
.btn{display:flex;align-items:center;justify-content:center;font-size:17px}
.btn-outline{left:799px;top:104px;width:147px;height:56px;border:1px solid var(--white);color:var(--white)}
.btn-solid{left:962px;top:104px;width:147px;height:56px;background:var(--white);color:var(--ink)}

/* services */
.section-title{font-size:36px;color:var(--black);letter-spacing:1px}
.help-title{left:0;top:1186px;width:1200px;text-align:center}
.service-img{width:310px;height:296px;top:1275px}
.service-label{width:310px;height:86px;top:1528px;background:var(--black);color:var(--white);display:flex;align-items:center;justify-content:space-between;padding:0 24px;font-size:20px}

/* about */
.about-img{left:446px;top:1761px;width:754px;height:545px;background:linear-gradient(135deg,#c9c3bb 0%,#a89b8e 45%,#7d7570 100%)}
.card{background:var(--white);box-shadow:0 4px 24px rgba(0,0,0,.12)}
.about-card{left:91px;top:1801px;width:582px;height:465px}
.about-card h2{position:absolute;left:64px;top:52px}
.about-card .body{position:absolute;left:64px;top:112px;width:480px;font-size:16px;line-height:32px;color:var(--muted)}
.about-card .body p+p{margin-top:10px}
.btn-dark{background:var(--black);color:var(--white);font-weight:700;font-size:15px;letter-spacing:1px}

/* blog */
.blog-img{left:0;top:2448px;width:753px;height:545px;background:linear-gradient(180deg,#b9c7d6 0%,#8d8f97 40%,#4f5a3e 75%,#2f3b25 100%)}
.blog-card{left:526px;top:2488px;width:580px;height:467px}
.blog-card h2{position:absolute;left:44px;top:44px}
.post-title{position:absolute;left:44px;top:108px;width:490px;font-size:16px;line-height:22px;font-weight:500;color:var(--ink)}
.post-meta{position:absolute;left:44px;top:160px;width:490px;display:flex;justify-content:space-between;font-size:14px;font-weight:700}
.post-excerpt{position:absolute;left:44px;top:205px;width:490px;font-size:16px;line-height:32px;color:var(--muted)}

/* ebook */
.ebook{left:0;top:3137px;width:1200px;height:337px;background:var(--dark);color:var(--white)}
.ebook h2{left:90px;top:66px;color:var(--white)}
.ebook p{left:90px;top:122px;width:560px;font-size:16px;line-height:26px;color:#d0d0d0}
.btn-pdf{left:91px;top:208px;width:254px;height:54px;border:1px solid var(--white);color:var(--white);gap:12px;font-size:16px}
.ebook-img{left:689px;top:3166px;width:420px;height:388px;background:linear-gradient(150deg,#d9d9d9 0%,#8a8a8a 35%,#5b3e2a 65%,#c0c0c0 100%);transform:rotate(-4deg);border-radius:6px}

/* footer */
.site-footer{left:0;top:3474px;width:1200px;height:535px;background:linear-gradient(180deg,#24303b 0%,#1a232b 50%,#0f151b 100%);color:var(--white)}
.col{top:182px}
.col h3{font-family:"Audiowide",sans-serif;text-transform:uppercase;font-weight:400;font-size:20px;letter-spacing:1px;margin-bottom:22px}
.col li{list-style:none;font-size:15px;line-height:34px;color:var(--light)}
.newsletter{left:804px;top:243px;width:305px;height:45px;background:var(--white);border-radius:23px;display:flex;align-items:center;justify-content:space-between;padding-left:24px;font-size:12px;color:#888}
.newsletter b{background:var(--black);color:var(--white);height:45px;width:104px;border-radius:23px;display:flex;align-items:center;justify-content:center;font-size:15px;font-weight:600}
.follow{left:804px;top:332px;font-family:"Audiowide",sans-serif;font-size:20px;text-transform:uppercase}
.social{left:806px;top:390px;display:flex;gap:26px}
.social i{width:14px;height:14px;border-radius:50%;background:var(--white);display:block}
.copyright{left:0;top:482px;width:1200px;text-align:center;font-size:12px;color:var(--light)}
</style>
</head>
<body>

<header class="site-header abs">
  <div class="brand abs"><span class="brand-mark"></span>TESSLY REALTY</div>
  <nav class="main-nav abs">
    <span>Home</span><span>About Us</span><span>Services</span><span>Contact Us</span><span>More</span><span class="caret"></span>
  </nav>
</header>

<div class="top-bar abs">
  <div class="contact abs">
    <span><svg width="14" height="14" viewBox="0 0 24 24"><path fill="#2a2a2a" d="M6.6 10.8a15 15 0 0 0 6.6 6.6l2.2-2.2c.3-.3.7-.4 1-.2 1.1.4 2.3.6 3.6.6.6 0 1 .4 1 1V20c0 .6-.4 1-1 1C10.6 21 3 13.4 3 4c0-.6.4-1 1-1h3.5c.6 0 1 .4 1 1 0 1.3.2 2.5.6 3.6.1.3 0 .7-.2 1z"/></svg>516-555-0147</span>
    <span><svg width="16" height="13" viewBox="0 0 24 18"><path fill="#2a2a2a" d="M0 0h24v2L12 10 0 2zM0 4.5l12 8 12-8V18H0z"/></svg>Email me</span>
  </div>
  <div class="account abs"><span>Have an account? Sign In</span><span>Create Account</span></div>
</div>

<section class="hero abs" role="img" aria-label="Photo of a tree-lined Brooklyn street with brick brownstones and stoops">
  <h1 class="hero-title display abs">Assisting landlords increase<br>profits while decreasing the stress.</h1>
  <svg class="play abs" viewBox="0 0 74 74"><circle cx="37" cy="37" r="37" fill="#fff"/><path d="M30 24 L52 37 L30 50 Z" fill="#111"/></svg>
  <div class="dots abs"><i class="on"></i><i></i><i></i><i></i></div>
</section>

<section class="intro abs">
  <h2 class="abs">Tessly Realty NYC specializes in assisting landlords</h2>
  <p class="abs">by increasing their profits while decreasing their stress.</p>
  <div class="btn btn-outline abs">Learn More</div>
  <div class="btn btn-solid abs">Contact us</div>
</section>

<h2 class="section-title display help-title abs">How we can help</h2>

<div class="service-img abs" style="left:91px;background:linear-gradient(160deg,#e8e6e2,#b8b0a6)" role="img" aria-label="Photo of a bright modern apartment interior with dining table"></div>
<div class="service-img abs" style="left:444px;background:linear-gradient(160deg,#9aa3ad,#6d5a4c)" role="img" aria-label="Photo of a multifamily brick building with fire escapes"></div>
<div class="service-img abs" style="left:799px;background:linear-gradient(180deg,#aab8c6,#7d8b6a 55%,#5a6a45)" role="img" aria-label="Aerial photo of Florida land and waterfront"></div>

<div class="service-label abs" style="left:75px">Multi-Family Leasing<span>&raquo;</span></div>
<div class="service-label abs" style="left:428px">Multi-Family Sales<span>&raquo;</span></div>
<div class="service-label abs" style="left:783px">Site Selection Advisory<span>&raquo;</span></div>

<div class="about-img abs" role="img" aria-label="Photo of a handshake over a contract with house keys"></div>
<section class="about-card card abs">
  <h2 class="section-title display">About Us</h2>
  <div class="body">
    <p>Tessly Realty NYC-PB is a full-service real estate brokerage firm with offices located in Brooklyn, New York and West Palm Beach, Florida. Our firm focuses on multifamily leasing, sales and Commercial Real Estate Site Selection Advisory.</p>
    <p>Our clients are private and institutional multifamily real estate investors.</p>
  </div>
  <div class="btn btn-dark abs" style="left:64px;top:355px;width:155px;height:46px">LEARN MORE</div>
</section>

<div class="blog-img abs" role="img" aria-label="Photo of the West Palm Beach skyline with palm trees"></div>
<section class="blog-card card abs">
  <h2 class="section-title display">Blog</h2>
  <div class="post-title">Brooklyn, NY To West Palm Beach Florida...The Best Of Both Worlds</div>
  <div class="post-meta"><span>By | General | 1 Comment</span><span>August 3, 2018</span></div>
  <div class="post-excerpt">Tessly Realty NYC is a full service real estate brokerage firm located in Brooklyn, NY and West Palm Beach, FL. We specialize in multifamily sales and leasing, short-sales and 1031 Exchange property appropriation...</div>
  <div class="btn btn-dark abs" style="left:44px;top:362px;width:155px;height:46px">READ MORE</div>
</section>

<section class="ebook abs">
  <h2 class="section-title display abs">Ebook</h2>
  <p class="abs">An ebook to be downloaded and information on my probate sales and multifamily leasing marketing campaigns</p>
  <div class="btn btn-pdf abs"><svg width="16" height="20" viewBox="0 0 16 20"><path d="M1 1h9l5 5v13H1z" fill="none" stroke="#fff" stroke-width="1.5"/><path d="M10 1v5h5" fill="none" stroke="#fff" stroke-width="1.5"/></svg>DOWNLOAD PDF</div>
</section>
<div class="ebook-img abs" role="img" aria-label="Ebook cover with a kitchen interior photo"></div>

<footer class="site-footer abs" role="img" aria-label="Faded aerial photo of a waterfront city at dusk">
  <div class="col abs" style="left:88px"><h3>Links</h3><ul><li>Home</li><li>About Us</li><li>Services</li><li>Contact Us</li><li>More</li></ul></div>
  <div class="col abs" style="left:286px"><h3>Specialising</h3><ul><li>Residential leasing</li><li>Multifamily sales</li><li>1031 Exchange</li><li>appropriation</li></ul></div>
  <div class="col abs" style="left:529px"><h3>Contact Us</h3><ul><li>561-555-0192</li><li>ava@tesslyrealty.com</li><li>214 Linden Ave. 3</li><li>Brooklyn, New York 11221</li></ul></div>
  <div class="col abs" style="left:804px"><h3>Newsletter</h3></div>
  <div class="newsletter abs">Enter Your Email Address<b>Send</b></div>
  <div class="follow abs">Follow Us</div>
  <div class="social abs"><i></i><i></i><i></i><i></i></div>
  <div class="copyright abs">Copyrights © 2019 The company Name. All Rights Reserved</div>
</footer>

</body>
</html>
```